Refer a Friend A5 Flyer for Healthcare Staff

We need an A5 flyer that we can hand out to existing and new staff members promoting our Refer a friend Scheme. We need the leaflet to encourage staff to talk to their family and friends about joining our Healthcare Agency, which provides staff to local care related establishments. Using our logo and brand colours blue and green, as per our website, the final design will need to clearly convey the benefits and attractions of referring additional staff to the team. In addition is the promotion of our Chatterbook page, requesting staff to like the page and to like and share various posts.

Target Market(s)

Healthcare and potential Healthcare Staff

Industry/Entity Type

Healthcare

Colors
33b8a4
3277b5

Requirements
Must have
• Company Logo, Brand colours,
• text; "Refer a Friend and receive a £50 Bonus after just 1 completed shift"
• text; "3 easy steps to refer a friend, 1 Fill out your name on the back of your Business Card 2 Hand the card to your friend or any person you wish to refer, 3 ask your friend to present the card to us when they attend their interview"
• text; "Like and share any of our Open Days on Chatterbook for a chance to win a prize, you can find us easily by searching @CarewellStaffingPartners"
• text; "Like our Page to stay up to date with our events and offers"
Nice to have
• care worker / elderly care / support worker pictures
• Content / pics from website www.carewellstaffingpartners.co.uk

```html
<!DOCTYPE html>
<html lang="en">
<head>
<meta charset="utf-8">
<title>Refer a Friend Flyer – Carewell Staffing</title>
<link rel="stylesheet" href="https://fonts.googleapis.com/css2?family=Lato:wght@400;700;900&family=Oswald:wght@500;600&family=Roboto+Condensed:wght@400;500&display=swap">
<style>
  :root {
    --brand-blue: #0b4fa3;
    --brand-blue-deep: #08489a;
    --brand-teal: #19a98f;
    --brand-teal-light: #5fcbb5;
    --ink: #3a3a3a;
    --white: #ffffff;
    --stage: #6b6b6b;
  }
  * { margin: 0; padding: 0; box-sizing: border-box; }
  html, body { width: 1200px; height: 1200px; overflow: hidden; }
  body { background: var(--stage); font-family: "Lato", sans-serif; position: relative; }

  .flyer {
    position: absolute; left: 218px; top: 112px;
    width: 765px; height: 990px; background: var(--white); overflow: hidden;
  }
  .flyer-shapes { position: absolute; inset: 0; }
  .abs { position: absolute; }

  .headline { left: 35px; top: 372px; color: var(--brand-blue); }
  .headline h1 { font-size: 42px; font-weight: 900; line-height: 1.05; letter-spacing: -0.3px; }
  .headline h2 { font-size: 24.5px; font-weight: 700; line-height: 1.3; margin-top: 2px; }
  .intro { left: 35px; top: 489px; width: 390px; font-size: 10.6px; font-weight: 700; color: var(--ink); line-height: 1.3; }

  .benefits-title { left: 35px; top: 566px; font-size: 22.5px; font-weight: 700; color: var(--brand-blue); }
  .benefits-lead { left: 35px; top: 602px; width: 390px; font-size: 10.8px; font-weight: 700; color: var(--ink); line-height: 1.3; }
  .benefits-list { list-style: none; font-size: 13px; font-weight: 700; color: #4a4a4a; }
  .benefits-list li { display: flex; align-items: center; gap: 12px; height: 19px; }
  .benefits-list svg { width: 14px; height: 14px; flex: none; }
  .list-a { left: 35px; top: 643px; }
  .list-b { left: 185px; top: 642px; }

  .brand-mark { left: 214px; top: 744px; display: flex; align-items: center; gap: 8px;
    font-size: 20px; font-weight: 400; color: var(--brand-blue); }
  .brand-mark .dot { width: 14px; height: 14px; border-radius: 50%; background: var(--brand-teal); }

  .bonus-badge { left: 452px; top: 244px; width: 280px; height: 280px; border-radius: 50%;
    background: var(--brand-blue-deep); color: var(--white); text-align: center; padding-top: 60px; }
  .bonus-badge .lead { font-size: 20px; font-weight: 700; line-height: 1.12; }
  .bonus-badge .amount { font-family: "Oswald", sans-serif; font-weight: 500; font-size: 52px; line-height: 1.15; }
  .bonus-badge .tail { font-size: 20px; font-weight: 700; line-height: 1.2; }

  .steps-title { left: 454px; top: 533px; width: 277px; height: 67px; border-radius: 22px;
    background: var(--brand-teal); color: var(--white); font-family: "Oswald", sans-serif;
    font-weight: 600; font-size: 18.5px; display: flex; align-items: center; justify-content: center; }
  .steps-card { left: 454px; top: 612px; width: 277px; height: 206px; background: var(--white);
    box-shadow: 0 8px 8px -6px rgba(0,0,0,.35); }
  .steps-rail { position: absolute; left: 21px; top: 20px; width: 2px; height: 110px; background: var(--brand-blue); }
  .step { position: absolute; left: 42px; width: 228px; font-family: "Roboto Condensed", sans-serif;
    font-size: 15.5px; color: #1f1f1f; line-height: 1.23; }
  .step-num { position: absolute; left: -33px; top: 1px; width: 19px; height: 19px; border-radius: 50%;
    background: var(--brand-blue); color: var(--white); font-size: 11px; font-weight: 500;
    display: flex; align-items: center; justify-content: center; }

  .social-promo { left: 35px; top: 836px; color: var(--white); line-height: 1.25; }
  .social-promo strong { font-size: 20px; font-weight: 700; display: block; }
  .social-promo span { font-size: 15px; font-weight: 400; display: block; }
  .social-promo b { font-weight: 700; }

  .like-pill { left: 454px; top: 842px; width: 277px; height: 70px; border-radius: 32px;
    background: var(--brand-blue-deep); color: var(--white); text-align: center;
    font-size: 14.5px; font-weight: 700; line-height: 1.2; display: flex; align-items: center;
    justify-content: center; box-shadow: 0 8px 8px -6px rgba(0,0,0,.35); }

  .footer { left: 0; top: 940px; width: 765px; height: 50px; display: flex; align-items: center; }
  .footer .join { margin-left: 35px; font-size: 22px; font-weight: 700; color: #2b2b2b; }
  .footer .url { margin-left: 52px; font-size: 17.5px; font-weight: 700; color: #2b2b2b; }
  .footer .social { margin-left: 102px; display: flex; gap: 9px; }
  .footer .social span { width: 32px; height: 32px; border-radius: 50%; background: #2b2b2b; }
</style>
</head>
<body>
<main class="flyer">
  <svg class="flyer-shapes" viewBox="0 0 765 990" width="765" height="990">
    <defs>
      <linearGradient id="photoTone" x1="0" y1="0" x2="1" y2="1">
        <stop offset="0" stop-color="#efe6d9"/>
        <stop offset=".5" stop-color="#c9b09a"/>
        <stop offset="1" stop-color="#e9e4de"/>
      </linearGradient>
    </defs>
    <rect class="photo-area" role="img" aria-label="Photograph of a smiling care worker in uniform walking arm in arm with an elderly woman" x="0" y="0" width="765" height="460" fill="url(#photoTone)"/>
    <path d="M0,395 Q200,220 462,332 L765,420 L765,990 L0,990Z" fill="#ffffff"/>
    <path d="M0,325 Q230,230 462,332 Q230,250 0,395Z" fill="var(--brand-teal)"/>
    <path d="M0,390 Q230,250 462,332 Q230,262 0,400Z" fill="var(--brand-teal-light)"/>
    <path d="M700,420 Q740,415 765,404 L765,455 Q735,462 700,460Z" fill="var(--brand-teal)"/>
    <path d="M0,722 Q250,875 470,752 L765,690 L765,940 L0,940Z" fill="var(--brand-teal)"/>
    <path d="M0,708 Q250,870 470,748" fill="none" stroke="var(--brand-blue)" stroke-width="5"/>
    <path d="M731,695 L765,702 L765,770 Q750,735 731,730Z" fill="var(--brand-blue)"/>
  </svg>

  <div class="abs headline">
    <h1>We supply qualified</h1>
    <h2>experienced local staff, dedicated to<br>delivering excellent services.</h2>
  </div>
  <p class="abs intro">We work with a wide range of Healthcare establishments throughout Kent and can accommodate candidates looking for either full time work or part time hours to fit around personal commitments. We also cater for people looking for the occasional shift in addition to a full time job to boost earnings.</p>

  <h3 class="abs benefits-title">The benefits of Joining</h3>
  <p class="abs benefits-lead">We want our staff members to feel valued and supported at all times, which is why we offer the following benefits of joining our team:</p>

  <ul class="abs benefits-list list-a">
    <li><svg viewBox="0 0 14 14"><circle cx="7" cy="7" r="6" fill="none" stroke="#0b4fa3" stroke-width="1.3"/><path d="M4,7.2 L6.2,9.3 L10,4.8" fill="none" stroke="#0b4fa3" stroke-width="1.6"/></svg>Free uniform</li>
    <li><svg viewBox="0 0 14 14"><circle cx="7" cy="7" r="6" fill="none" stroke="#0b4fa3" stroke-width="1.3"/><path d="M4,7.2 L6.2,9.3 L10,4.8" fill="none" stroke="#0b4fa3" stroke-width="1.6"/></svg>Free DBS</li>
    <li><svg viewBox="0 0 14 14"><circle cx="7" cy="7" r="6" fill="none" stroke="#0b4fa3" stroke-width="1.3"/><path d="M4,7.2 L6.2,9.3 L10,4.8" fill="none" stroke="#0b4fa3" stroke-width="1.6"/></svg>Free training</li>
    <li><svg viewBox="0 0 14 14"><circle cx="7" cy="7" r="6" fill="none" stroke="#0b4fa3" stroke-width="1.3"/><path d="M4,7.2 L6.2,9.3 L10,4.8" fill="none" stroke="#0b4fa3" stroke-width="1.6"/></svg>Weekly Pay</li>
    <li><svg viewBox="0 0 14 14"><circle cx="7" cy="7" r="6" fill="none" stroke="#0b4fa3" stroke-width="1.3"/><path d="M4,7.2 L6.2,9.3 L10,4.8" fill="none" stroke="#0b4fa3" stroke-width="1.6"/></svg>Holiday pay</li>
  </ul>
  <ul class="abs benefits-list list-b">
    <li><svg viewBox="0 0 14 14"><circle cx="7" cy="7" r="6" fill="none" stroke="#0b4fa3" stroke-width="1.3"/><path d="M4,7.2 L6.2,9.3 L10,4.8" fill="none" stroke="#0b4fa3" stroke-width="1.6"/></svg>A broad range of assignments</li>
    <li><svg viewBox="0 0 14 14"><circle cx="7" cy="7" r="6" fill="none" stroke="#0b4fa3" stroke-width="1.3"/><path d="M4,7.2 L6.2,9.3 L10,4.8" fill="none" stroke="#0b4fa3" stroke-width="1.6"/></svg>Flexible working hours</li>
    <li><svg viewBox="0 0 14 14"><circle cx="7" cy="7" r="6" fill="none" stroke="#0b4fa3" stroke-width="1.3"/><path d="M4,7.2 L6.2,9.3 L10,4.8" fill="none" stroke="#0b4fa3" stroke-width="1.6"/></svg>Friendly and helpful office staff</li>
  </ul>

  <div class="abs brand-mark"><span class="dot"></span>Carewell Staffing</div>

  <div class="abs bonus-badge">
    <div class="lead">Refer a Friend and<br>receive a</div>
    <div class="amount">£50 Bonus</div>
    <div class="tail">after just<br>1 completed shift"</div>
  </div>

  <div class="abs steps-title">3 EASY STEPS TO REFER A FRIEND</div>
  <div class="abs steps-card">
    <span class="steps-rail"></span>
    <p class="step" style="top:14px"><span class="step-num">1</span>Fill out your name on the back of your Business Card</p>
    <p class="step" style="top:64px;left:46px"><span class="step-num" style="left:-37px">2</span>Hand the card to your friend or any person you wish to refer,</p>
    <p class="step" style="top:117px"><span class="step-num">3</span>ask your friend to present the card to us when they attend their interview</p>
  </div>

  <div class="abs social-promo">
    <strong>Like and share any of our Open Days on</strong>
    <span>Chatterbook for a chance to win a prize,</span>
    <span>you can find us easily by</span>
    <span>searching <b>@CarewellStaffingPartners"</b></span>
  </div>

  <div class="abs like-pill">Like our Page to stay up to date with<br>our events and offers</div>

  <footer class="abs footer">
    <span class="join">Join us</span>
    <span class="url">www.carewellstaffingpartners.co.uk</span>
    <span class="social"><span></span><span></span></span>
  </footer>
</main>
</body>
</html>
```